Need a business card design for a residential architect.

You can get a sense of his work at www.tberlove.com

Would like a consistent look and feel between business card and website
.

Target Market(s)

Residential homeowners builders

Industry/Entity Type

Residential

Contact Information for Business Card

Dale Morrick
Principle
Morrick Architecture
418 Kestrel Lane
Alder Falls, CA 95017

dale@tberlove.com

tberlove.com
phone: 650-555-2716
Fax: 650-555-8043

Font styles to use
Sans Serif

Requirements
Must have
• Details above
Nice to have
• Would like a consistent look and feel between business card and website
Should not have
• None

```html
<!DOCTYPE html>
<html lang="en">
<head>
<meta charset="utf-8">
<title>Morrick Architecture – Business Card</title>
<link rel="stylesheet" href="https://fonts.googleapis.com/css2?family=Open+Sans:wght@400;600;700&display=swap">
<style>
  :root {
    --page: #ececec;
    --card: #f7f7f7;
    --ink: #1a1a1a;
    --grey: #7a7a7a;
    --grey-band: #737373;
    --grey-soft: #a9a9a9;
    --black: #050505;
    --white: #ffffff;
  }
  * { box-sizing: border-box; margin: 0; padding: 0; }
  html, body { width: 1200px; height: 1001px; overflow: hidden; }
  body {
    background: var(--page);
    font-family: "Open Sans", Arial, sans-serif;
    display: flex;
    align-items: center;
    justify-content: center;
    gap: 40px;
  }
  .card {
    position: relative;
    width: 520px;
    height: 297px;
    overflow: hidden;
    box-shadow: 0 6px 18px rgba(0,0,0,0.12);
  }
  .card-front { background: var(--card); }
  .card-back { background: var(--black); display: flex; align-items: center; justify-content: center; }

  .wave { position: absolute; inset: 0; width: 100%; height: 100%; }

  .brand {
    font-weight: 600;
    text-transform: uppercase;
    letter-spacing: 0.14em;
    line-height: 1;
  }
  .card-front .brand {
    position: absolute;
    left: 30px;
    top: 30px;
    font-size: 20px;
    color: var(--grey);
  }
  .card-back .brand {
    font-size: 30px;
    color: var(--white);
  }

  .contact-list {
    position: absolute;
    left: 30px;
    top: 70px;
    list-style: none;
    font-size: 12px;
    color: var(--ink);
  }
  .contact-list li {
    display: flex;
    align-items: center;
    gap: 8px;
    height: 16px;
  }
  .contact-list svg { width: 10px; height: 10px; fill: var(--grey); flex: none; }

  .person {
    position: absolute;
    right: 30px;
    top: 150px;
    text-align: right;
  }
  .person-name { font-size: 15px; font-weight: 700; color: var(--ink); }
  .person-title { font-size: 11px; color: var(--grey); }

  .website {
    position: absolute;
    right: 30px;
    bottom: 22px;
    font-size: 17px;
    font-weight: 700;
    color: var(--white);
  }
</style>
</head>
<body>

<section class="card card-front" aria-label="Business card front">
  <svg class="wave" viewBox="0 0 520 297" preserveAspectRatio="none" aria-hidden="true">
    <path d="M0,128 C110,200 300,222 520,200" fill="none" stroke="var(--grey-soft)" stroke-width="2"/>
    <path d="M0,138 C110,212 300,232 520,212 L520,218 C300,242 110,222 0,152 Z" fill="var(--black)"/>
    <path d="M0,168 C120,238 300,250 520,232 L520,297 L0,297 Z" fill="var(--grey-band)"/>
  </svg>

  <div class="brand">Morrick Architecture</div>

  <ul class="contact-list">
    <li><svg viewBox="0 0 10 10"><path d="M5 0a3.5 3.5 0 0 0-3.5 3.5C1.5 6 5 10 5 10s3.5-4 3.5-6.5A3.5 3.5 0 0 0 5 0zm0 5a1.5 1.5 0 1 1 0-3 1.5 1.5 0 0 1 0 3z"/></svg>418 Kestrel Lane Alder Falls, CA 95017</li>
    <li><svg viewBox="0 0 10 10"><path d="M0 2h10v6H0z M0 2l5 3.5L10 2" stroke="var(--card)" stroke-width="0.8"/></svg>dale@tberlove.com</li>
    <li><svg viewBox="0 0 10 10"><path d="M1 3h8v6H1z M2 1h6v2H2z"/></svg>650-555-2716</li>
    <li><svg viewBox="0 0 10 10"><path d="M1 4h8v5H1z M2.5 0h5v4h-5z"/></svg>650-555-8043</li>
  </ul>

  <div class="person">
    <div class="person-name">Dale Morrick</div>
    <div class="person-title">Principle</div>
  </div>

  <div class="website">www.tberlove.com</div>
</section>

<section class="card card-back" aria-label="Business card back">
  <div class="brand">Morrick Architecture</div>
</section>

</body>
</html>
```